Manufacturer's Representative Group needs a clean new Website

We represent and sell a number of suppliers that design and build products used in Biopharmaceutical manufacturing. Our sales region is in the central US. Our customer base is scientific / engineering based - so clean, we organized design with a focus on the products - easy and clear navigation is necessary. We do not sell direct or warehouse product - so e-commerce is not needed. Our customers will use the website for reference on what we do and offer - we will use the site as a platform to present products from each vendor and the home page will be used to capture an overview and draw users deeper into the site. You can view our current site - which needs A LOT of help to get ideas on products represented and types of products

Target Market(s)

Engineers and Pharmaceutical / Bio pharm end users

Industry/Entity Type

E-Commerce

Number of Pages Required

2 page

Font styles to use
Sans Serif

Requirements
Must have
• I need a home page that provides a snapshot of my company and the product lines we represent - then a second page that I can copy as a template for each line I rep as well as for an "About us / contact" page.
• I would like to be able to manage content on the pages so something easy to adjust pictures or add content is a must
• Must use our logo

```html
<!DOCTYPE html>
<html lang="en">
<head>
<meta charset="utf-8">
<title>Prairie Bio — Home</title>
<link href="https://fonts.googleapis.com/css2?family=Open+Sans:wght@400;600;700&family=Montserrat:wght@500;600&display=swap" rel="stylesheet">
<style>
:root{
  --navy:#2b2870;
  --navy-deep:#25215f;
  --orange:#f1582a;
  --ink:#222;
  --muted:#444;
  --panel:#f4f4f4;
  --card:#f2f2f2;
  --rule:#d6d6d6;
  --white:#fff;
}
*{box-sizing:border-box;margin:0;padding:0}
html,body{width:732px;height:1200px;overflow:hidden;background:var(--white)}
body{position:relative;font-family:"Open Sans",Arial,sans-serif;color:var(--ink)}
.abs{position:absolute}

/* header */
.site-header{left:0;top:0;width:732px;height:72px;border-bottom:2px solid var(--orange)}
.brand{left:62px;top:18px;display:flex;align-items:center;gap:8px;font-family:"Montserrat",Arial,sans-serif;font-weight:500;font-size:24px;color:var(--navy)}
.brand-dot{width:14px;height:14px;border-radius:50%;background:var(--orange)}
.main-nav{right:60px;top:39px;display:flex;height:31px}
.main-nav a{display:block;padding:0 19px;line-height:31px;font-size:12px;color:#333;text-decoration:none}
.main-nav a.active{background:var(--orange);color:var(--white);border-radius:2px 2px 0 0}

/* hero */
.hero{left:0;top:72px;width:732px;height:300px;background:linear-gradient(180deg,#2f2b7c,#3a358d 60%,#2c2874)}
.hero-frame{left:61px;top:18px;width:610px;height:255px;background:var(--white);padding:6px;box-shadow:0 6px 10px rgba(0,0,0,.35)}
.hero-photo{width:100%;height:100%;background:linear-gradient(90deg,#c9d8ee 0%,#e9f0fa 30%,#2aa6a0 48%,#d9e4f3 62%,#3a6bd0 78%,#e3ecf8 100%)}

/* about */
.about{left:0;top:372px;width:732px;height:153px;background:#f8f8f8}
.section-title{display:flex;align-items:center;font-family:"Montserrat",Arial,sans-serif;font-weight:600;font-size:13px;color:var(--navy-deep)}
.section-title em{font-style:normal;color:var(--orange);margin-left:4px}
.section-title .rule{flex:1;height:1px;background:var(--rule);margin-left:14px;position:relative}
.section-title .rule::before{content:"";position:absolute;left:-4px;top:-4px;width:8px;height:8px;border-radius:50%;background:#cfcfcf}
.about .section-title{left:67px;top:20px;width:570px}
.about-copy{left:67px;top:45px;width:582px;font-size:7.2px;line-height:12.2px;color:var(--ink)}

/* feature cards */
.card{top:545px;width:141px;height:193px;background:var(--card)}
.card h3{margin-top:10px;text-align:center;font-family:"Montserrat",Arial,sans-serif;font-weight:500;font-size:11.5px;letter-spacing:.5px;color:var(--navy-deep)}
.card-photo{margin:8px auto 0;width:128px;height:76px}
.card p{margin:6px 7px 0;font-size:7.3px;line-height:9.8px;text-align:justify;color:var(--muted)}
.btn-more{position:absolute;left:5px;bottom:12px;width:131px;height:18px;background:var(--orange);color:var(--white);font-size:8px;line-height:18px;text-align:center;text-decoration:none}

/* products */
.products .section-title{left:64px;top:787px;width:378px}
.product{left:64px;width:392px;display:flex;align-items:center}
.vendor-mark{width:126px;flex:none;font-family:"Montserrat",Arial,sans-serif;font-weight:600;font-size:11.5px;color:var(--navy-deep);text-align:center;white-space:nowrap}
.product-text{font-size:7.2px;line-height:11px;color:var(--muted)}
.product-text strong{display:block;color:#222;font-weight:600}

/* enquiry */
.enquiry{left:472px;top:795px;width:197px;height:327px;background:var(--panel)}
.enquiry h3{position:absolute;left:20px;top:10px;width:158px;padding-bottom:6px;border-bottom:1px dotted #bbb;font-family:"Montserrat",Arial,sans-serif;font-weight:600;font-size:13px;letter-spacing:.8px;color:var(--navy-deep)}
.enquiry p{position:absolute;left:20px;top:47px;width:160px;font-size:7.2px;line-height:11px;color:#333}
.field{position:absolute;left:18px;width:154px;height:22px;border:1px solid #ccc;border-radius:11px;background:var(--white);font-size:7.3px;line-height:20px;padding-left:12px;color:#444;box-shadow:inset 0 1px 2px rgba(0,0,0,.08)}
.field.area{left:21px;width:151px;height:80px;border-radius:8px;line-height:1;padding-top:10px}
.btn-submit{position:absolute;left:103px;top:292px;width:66px;height:20px;border-radius:7px;background:var(--navy-deep);color:var(--white);font-size:7.6px;font-weight:600;line-height:20px;text-align:center}

/* footer */
.site-footer{left:0;top:1139px;width:732px;height:61px;background:var(--navy-deep);border-top:2px solid var(--orange)}
.footer-nav{left:66px;top:14px;font-size:9.3px;color:var(--white);word-spacing:2px}
.footer-nav span{margin:0 14px}
.copyright{left:66px;top:31px;font-size:9px;color:var(--white)}
.footer-brand{right:66px;top:14px;display:flex;align-items:center;gap:8px;font-family:"Montserrat",Arial,sans-serif;font-weight:500;font-size:20px;color:var(--white)}
.footer-brand .brand-dot{width:12px;height:12px;background:var(--white)}
</style>
</head>
<body>

<header class="site-header abs">
  <div class="brand abs"><span class="brand-dot"></span>Prairie Bio</div>
  <nav class="main-nav abs">
    <a class="active" href="#">HOME</a>
    <a href="#">Contact Us</a>
    <a href="#">Products</a>
  </nav>
</header>

<section class="hero abs">
  <div class="hero-frame abs">
    <div class="hero-photo" role="img" aria-label="Laboratory glassware filled with coloured liquids"></div>
  </div>
</section>

<section class="about abs">
  <h2 class="section-title abs">About <em>Prairie Bio</em><span class="rule"></span></h2>
  <div class="about-copy abs">
    We should use the same text that is on the current website unless something else should be added. (Add an image of some sort depicting about us.&nbsp; Image of some products could do)<br>
    The current site seems too plain at the moment and I believe it is because of lack of text or images.<br>
    We could add more links to the side of the page linking to images on the site or text explaining what some of the products we carry are.<br>
    Such as a Link to PET and we could have a text from Omnipedia explaining what PET is.<br>
    Same for PET Resin,&nbsp; PET Bottles, P.E., P.P., Atomizers, sprayers, molds, etc. (I will be providing the text for these items as well as images, if none are found by the designer).
  </div>
</section>

<article class="card abs" style="left:61px">
  <h3>LOREM IPSUM</h3>
  <div class="card-photo" role="img" aria-label="Single-use assembly components" style="background:linear-gradient(135deg,#2b3f63,#8fa7c4 55%,#2a3b58)"></div>
  <p>Lorem Ipsum is simply dummy text of the pring and typesetting industry. Lorem Ipsum has been the industry's standard.</p>
  <a class="btn-more" href="#">Readmore</a>
</article>
<article class="card abs" style="left:217px">
  <h3>LOREM IPSUM</h3>
  <div class="card-photo" role="img" aria-label="Peristaltic pump unit" style="background:linear-gradient(135deg,#9bbfe3,#3b63a8 55%,#c9d6e6)"></div>
  <p>Lorem Ipsum is simply dummy text of the pring and typesetting industry. Lorem Ipsum has been the industry's standard.</p>
  <a class="btn-more" href="#">Readmore</a>
</article>
<article class="card abs" style="left:372px">
  <h3>LOREM IPSUM</h3>
  <div class="card-photo" role="img" aria-label="Red liquid filling pump" style="background:linear-gradient(135deg,#c71d22,#e2574a 60%,#e8d8c6)"></div>
  <p>Lorem Ipsum is simply dummy text of the pring and typesetting industry. Lorem Ipsum has been the industry's standard.</p>
  <a class="btn-more" href="#">Readmore</a>
</article>
<article class="card abs" style="left:528px">
  <h3>LOREM IPSUM</h3>
  <div class="card-photo" role="img" aria-label="Bioprocess equipment installation" style="background:linear-gradient(135deg,#e8e8e8,#9a9a9a 50%,#dcdcdc)"></div>
  <p>Lorem Ipsum is simply dummy text of the pring and typesetting industry. Lorem Ipsum has been the industry's standard.</p>
  <a class="btn-more" href="#">Readmore</a>
</article>

<section class="products">
  <h2 class="section-title abs">Our Products<span class="rule"></span></h2>

  <div class="product abs" style="top:832px">
    <div class="vendor-mark">Flexline Tubing Co.</div>
    <div class="product-text"><strong>Specialist manufacturers of PTFE lined flexible hoses</strong>Concept, design and production of single use assemblies, custom carboys, tubing manifolds and other products designed for cGMP applications</div>
  </div>
  <div class="product abs" style="top:885px">
    <div class="vendor-mark">PureSeal</div>
    <div class="product-text"><strong>PureSeal®, Inc. provides cGMP manufactured components.</strong>Concept, design and production of single use assemblies, custom carboys, tubing manifolds and other products designed for cGMP applications</div>
  </div>
  <div class="product abs" style="top:943px">
    <div class="vendor-mark">FillMotion</div>
    <div class="product-text"><strong>FillMotion peristaltic liquid filling pumps, controls and systems</strong>Concept, design and production of single use assemblies, custom carboys, tubing manifolds and other products designed for cGMP applications</div>
  </div>
  <div class="product abs" style="top:1003px">
    <div class="vendor-mark">Refina</div>
    <div class="product-text"><strong>Refina Solutions offers an for bio-process management</strong>Concept, design and production of single use assemblies, custom carboys, tubing manifolds and other products designed for cGMP applications</div>
  </div>
  <div class="product abs" style="top:1067px">
    <div class="vendor-mark">Argent Polymers</div>
    <div class="product-text"><strong>Argent Polymers pioneers in silicone</strong>Concept, design and production of single use assemblies, custom carboys, tubing manifolds and other products designed for cGMP applications</div>
  </div>
</section>

<aside class="enquiry abs">
  <h3>QUICK ENQUIRY</h3>
  <p>In hac habitasse platea dictumst. Donec commodo, purus sit amet luctus placerat, nunc nulla congue enim, vitae vulputate mauris ligula nec orci.</p>
  <div class="field" style="top:101px">Your Name</div>
  <div class="field" style="top:132px">Your Email</div>
  <div class="field" style="top:164px">Your Phone</div>
  <div class="field area" style="top:197px">Additional Information</div>
  <div class="btn-submit">Submit Form</div>
</aside>

<footer class="site-footer abs">
  <div class="footer-nav abs">Home<span>|</span>Contact Us<span>|</span>Products</div>
  <div class="copyright abs">© Prairie Biosolutions, Corp.</div>
  <div class="footer-brand abs"><span class="brand-dot"></span>Prairie Bio</div>
</footer>

</body>
</html>
```